skincare creams for tired moms

I need a package and a logo design for a skincare company based in California called Petal Ledger. I make day and night cream, under eye cream, and body lotion. The first product I plan to launch is an under eye cream. It does not have to be in these colors but I do teals, greens, black, and cobalt blue.

The package is going to either be in a box or a bag. Either way I go it will be like a gift box or bag. The design should make the person feel like they are getting something special and luxurious just for them.
Updates

I have small kids and it is really difficult to find a chunk of time to myself to update or review.

Need extra days to review

Target Market(s)

mainly first time moms. I am making an under eye cream that does not use retinol but is still powerful enough to get rid of bags and dark circles.

Industry/Entity Type

Cosmetics

Logo Text

The package and logo should incorporate the name Petal Ledger.

Font styles to use
Decorative
Script

Colors

Designer to choose colors to be used in the design.

Requirements
Nice to have
• maybe focus more on Ledger instead of Petal. Also incorporate plants or flowers
Should not have
• not a huge fan of pink

```html
<!DOCTYPE html>
<html lang="en">
<head>
<meta charset="utf-8">
<title>Petal Ledger – Under Eye Cream Label</title>
<link rel="stylesheet" href="https://fonts.googleapis.com/css2?family=Barlow+Condensed:wght@300&display=swap">
<style>
  :root {
    --stage: #3a3a3c;
    --paper: #ffffff;
    --teal: #138784;
    --teal-soft: #5fb3b0;
  }
  * { margin: 0; padding: 0; box-sizing: border-box; }
  html, body {
    width: 1200px;
    height: 845px;
    overflow: hidden;
    background: var(--stage);
  }
  .canvas {
    position: relative;
    width: 1200px;
    height: 845px;
    font-family: "Barlow Condensed", "Arial Narrow", sans-serif;
    font-weight: 300;
  }
  .label {
    position: absolute;
    left: 363px;
    top: 65px;
    width: 474px;
    height: 714px;
    background: var(--paper);
  }
  .band {
    position: absolute;
    left: 131px;
    width: 211px;
    background: var(--teal);
    color: var(--paper);
    text-align: center;
  }
  .band--top { top: 0; height: 413px; }
  .band--bottom { top: 563px; height: 151px; }
  .zigzag {
    position: absolute;
    left: 131px;
    width: 211px;
    height: 8px;
    display: block;
  }
  .zigzag--top { top: 413px; }
  .zigzag--bottom { top: 555px; }

  .brand-mark {
    position: absolute;
    top: 118px;
    left: 0;
    width: 100%;
    display: flex;
    align-items: center;
    justify-content: center;
    gap: 6px;
    font-size: 15px;
    letter-spacing: 0.02em;
  }
  .brand-mark__dot {
    width: 8px;
    height: 8px;
    border-radius: 50%;
    background: var(--paper);
  }
  .brand-name {
    position: absolute;
    top: 180px;
    left: 0;
    width: 100%;
    font-size: 47px;
    line-height: 50px;
  }
  .botanical {
    position: absolute;
    top: 298px;
    left: 73px;
    width: 66px;
    height: 100px;
    border-radius: 40% 40% 30% 30%;
    background: radial-gradient(circle at 50% 45%, var(--teal-soft), var(--teal) 75%);
  }
  .product-name {
    position: absolute;
    top: 440px;
    left: 0;
    width: 100%;
    text-align: center;
    color: var(--teal);
    font-size: 46px;
    line-height: 51px;
  }
  .ingredients {
    position: absolute;
    top: 36px;
    left: 0;
    width: 100%;
    font-size: 24px;
    line-height: 33px;
  }
</style>
</head>
<body>
<main class="canvas">
  <section class="label">
    <div class="band band--top">
      <div class="brand-mark">
        <span class="brand-mark__dot"></span>
        <span>Petal Ledger</span>
      </div>
      <h1 class="brand-name">Petal<br>Ledger</h1>
      <div class="botanical" role="img" aria-label="Line drawing of a leafy sprig with small berries"></div>
    </div>
    <svg class="zigzag zigzag--top" viewBox="0 0 211 8" preserveAspectRatio="none" aria-hidden="true">
      <polygon fill="#138784" points="0,0 211,0 211,8 202.2,0 193.4,8 184.6,0 175.8,8 167,0 158.2,8 149.4,0 140.6,8 131.8,0 123,8 114.2,0 105.5,8 96.7,0 87.9,8 79.1,0 70.3,8 61.5,0 52.7,8 43.9,0 35.1,8 26.3,0 17.5,8 8.7,0 0,8"/>
    </svg>

    <h2 class="product-name">under<br>eye cream</h2>

    <svg class="zigzag zigzag--bottom" viewBox="0 0 211 8" preserveAspectRatio="none" aria-hidden="true">
      <polygon fill="#138784" points="0,8 211,8 211,0 202.2,8 193.4,0 184.6,8 175.8,0 167,8 158.2,0 149.4,8 140.6,0 131.8,8 123,0 114.2,8 105.5,0 96.7,8 87.9,0 79.1,8 70.3,0 61.5,8 52.7,0 43.9,8 35.1,0 26.3,8 17.5,0 8.7,8 0,0"/>
    </svg>
    <div class="band band--bottom">
      <p class="ingredients">Hyaluronic acid+<br>clarixyl eyelume</p>
    </div>
  </section>
</main>
</body>
</html>
```